TPW other templates

1) Internal pages for the documents that we write. basically what will the pages inside look like. It should basically be a document with a header, a footer and a page number locator. It should include the following information: name of the report, date, TPW logo somehow, and version (draft, final etc). the information should be divided between header and footer. let me know if its unclear. As with everything it should work both in black and white and in color in case it is printed in black and white :-)
2) chapter dividers. This are the pages that you might have inside the report to separate sections. It should just have a page number, and chapter or section name. Simple, but again follow the same idea of the design that you created. It should be possible to have a picture in the divider, but it should not be a must. so in that sense we need to versions.
3) Business cards. Should include space for name, title, phone numbers (2 or 3), email, Skype, web page, and the company address which you have already.
4) a signature for emails. Basically the file that is glued to the bottom off all emails as a signature. Again it should include all the information in the business cards.

Not including any files since you have already designed others

```html
<!DOCTYPE html>
<html lang="en">
<head>
<meta charset="utf-8">
<title>TPW Business Card</title>
<link href="https://fonts.googleapis.com/css2?family=Ubuntu:wght@300;400;500;700&display=swap" rel="stylesheet">
<style>
  :root {
    --backdrop: #d3e0e6;
    --card-blue: #7ac4e2;
    --card-blue-light: #a6d8ee;
    --card-white: #ffffff;
    --brand-navy: #2b3f9e;
    --brand-blue: #3f6fc4;
    --ink: #4a4f55;
    --ink-soft: #7a8087;
    --rule: #a9d3e6;
    --band: #dcecf5;
    --icon: #4aa6d6;
  }
  * { box-sizing: border-box; margin: 0; padding: 0; }
  html, body { width: 1200px; height: 1000px; overflow: hidden; }
  body {
    background: var(--backdrop);
    font-family: "Ubuntu", sans-serif;
    position: relative;
  }
  .card {
    position: absolute;
    width: 520px;
    height: 310px;
    overflow: hidden;
    box-shadow: 0 6px 14px rgba(40, 60, 75, 0.18);
  }
  .card-front { left: 80px; top: 110px; background: var(--card-blue); }
  .card-back { left: 600px; top: 580px; background: var(--card-white); }

  .front-wave-area {
    position: absolute;
    inset: 0;
    background: linear-gradient(160deg, var(--card-blue) 0%, var(--card-blue) 35%, var(--card-blue-light) 60%, var(--card-blue) 85%);
    opacity: 0.8;
  }
  .front-wordmark {
    position: absolute;
    left: 0; right: 0; top: 118px;
    text-align: center;
    font-weight: 700;
    font-size: 76px;
    letter-spacing: 4px;
    color: var(--card-white);
    line-height: 1;
  }

  .back-edge-band {
    position: absolute;
    left: 0; top: 0; bottom: 0;
    width: 44px;
    background: linear-gradient(90deg, var(--card-blue-light) 0%, var(--band) 55%, var(--card-white) 100%);
  }
  .back-brand {
    position: absolute;
    right: 34px; top: 28px;
    text-align: right;
  }
  .back-wordmark {
    font-weight: 700;
    font-size: 44px;
    letter-spacing: 2px;
    color: var(--brand-navy);
    line-height: 1;
  }
  .company-name { font-size: 9.5px; color: var(--brand-blue); margin-top: 6px; }
  .company-address { font-size: 9.5px; color: var(--ink-soft); line-height: 1.35; }
  .divider-rule {
    position: absolute;
    left: 60px; right: 34px; top: 160px;
    border-top: 1px solid var(--rule);
  }
  .person { position: absolute; left: 70px; top: 188px; }
  .person-name { font-size: 18px; color: var(--ink); }
  .person-title { font-size: 13px; color: var(--ink); margin-top: 2px; }
  .contact-list {
    position: absolute;
    left: 70px; top: 238px;
    font-size: 11.5px;
    color: var(--ink);
  }
  .contact-row { display: flex; align-items: center; height: 22px; }
  .contact-item { display: flex; align-items: center; gap: 6px; white-space: nowrap; width: 104px; }
  .sep { color: var(--ink-soft); width: 18px; text-align: center; }
  .icon { width: 11px; height: 11px; flex: none; }
</style>
</head>
<body>

<section class="card card-front" aria-label="Business card front">
  <div class="front-wave-area" role="img" aria-label="Soft light blue wave pattern"></div>
  <div class="front-wordmark">TPW</div>
</section>

<section class="card card-back" aria-label="Business card back">
  <div class="back-edge-band" role="img" aria-label="Soft light blue wave along the left edge"></div>

  <div class="back-brand">
    <div class="back-wordmark">TPW</div>
    <p class="company-name">Tidewater Planning Works</p>
    <p class="company-address">Strandveien 18,<br>0252 Oslo, Norway</p>
  </div>

  <div class="divider-rule"></div>

  <div class="person">
    <p class="person-name">Erik Hansen</p>
    <p class="person-title">Managing Director</p>
  </div>

  <div class="contact-list">
    <div class="contact-row">
      <span class="contact-item">
        <svg class="icon" viewBox="0 0 12 12" aria-hidden="true"><path d="M2.5 1 L4.5 1 L5.2 3.6 L4 4.6 C4.7 6 5.9 7.3 7.4 8 L8.4 6.8 L11 7.5 L11 9.5 C11 10.3 10.3 11 9.5 11 C5 11 1 7 1 2.5 C1 1.7 1.7 1 2.5 1 Z" fill="var(--icon)"/></svg>
        +47 23550100
      </span>
      <span class="sep">|</span>
      <span class="contact-item">+47 23550101</span>
      <span class="sep">|</span>
      <span class="contact-item">+47 23550102</span>
    </div>
    <div class="contact-row">
      <span class="contact-item">
        <svg class="icon" viewBox="0 0 12 12" aria-hidden="true"><rect x="1" y="2.5" width="10" height="7" rx="1" fill="var(--icon)"/><path d="M1.5 3 L6 6.5 L10.5 3" stroke="#fff" stroke-width="1" fill="none"/></svg>
        post@tpw.no
      </span>
      <span class="sep">|</span>
      <span class="contact-item">
        <svg class="icon" viewBox="0 0 12 12" aria-hidden="true"><circle cx="6" cy="6" r="5" fill="none" stroke="var(--icon)" stroke-width="1.2"/><ellipse cx="6" cy="6" rx="2.2" ry="5" fill="none" stroke="var(--icon)" stroke-width="1"/><path d="M1 6 H11" stroke="var(--icon)" stroke-width="1"/></svg>
        www.tpw.no
      </span>
      <span class="sep">|</span>
      <span class="contact-item">
        <svg class="icon" viewBox="0 0 12 12" aria-hidden="true"><circle cx="6" cy="6" r="5" fill="var(--icon)"/></svg>
        Erik.Hansen
      </span>
    </div>
  </div>
</section>

</body>
</html>
```